Mira Bloom Fitness Coaching Project

I am a personal trainer based in London. My services include one-on-one PT sessions, bootcamps.
I would like the design to be minimalistic. With light colours: white, pink, purple.
I specialise in weight loss, flexibility, mobility.

Tessa Brogan
Personal Trainer
Email: tessa.brogan@quellmail.com
tel: 07700218493
Snapgram: Mira Bloom

Target Market(s)

adults, mostly females (age 18-50).

Industry/Entity Type

Fitness

Contact Information for Business Card

Tessa Brogan
Personal Trainer
tel: 07700218493
Snapgram: Mira Bloom

Font styles to use
Serif

Colors
eea4c8
fbd4d5
fdf9cf
cfeae6
cee9f5

Requirements
Nice to have
• minimalistic style
• easy to read and remember

```html
<!DOCTYPE html>
<html lang="en">
<head>
<meta charset="utf-8">
<title>Mira Bloom Fitness Coaching – Business Card</title>
<link rel="stylesheet" href="https://fonts.googleapis.com/css2?family=Open+Sans:ital,wght@0,400;0,700;1,400&family=Russo+One&display=swap">
<style>
  :root {
    --bg: #e4e4e4;
    --cream: #fdf9cf;
    --blush: #fbd4d5;
    --pink: #eea4c8;
    --white: #ffffff;
    --ink: #111111;
    --mark-grey: #e8e8e8;
    --muted: #555555;
  }
  html, body {
    margin: 0;
    width: 1200px;
    height: 1000px;
    overflow: hidden;
    background: var(--bg);
    font-family: "Open Sans", Arial, sans-serif;
  }
  .sheet {
    position: relative;
    width: 1200px;
    height: 1000px;
  }
  .card {
    position: absolute;
    left: 250px;
    width: 700px;
    height: 400px;
    overflow: hidden;
    box-shadow: 0 6px 18px rgba(0,0,0,0.18);
  }
  .card--front { top: 60px; background: var(--blush); }
  .card--back { top: 540px; background: var(--white); }

  /* Front */
  .front-split { position: absolute; inset: 0; }
  .brand-mark {
    position: absolute;
    display: flex;
    align-items: center;
    gap: 14px;
  }
  .card--front .brand-mark { left: 225px; top: 150px; }
  .brand-mark__square {
    width: 44px;
    height: 44px;
    background: var(--mark-grey);
  }
  .brand-mark__name {
    font-weight: 700;
    font-size: 28px;
    color: var(--ink);
    letter-spacing: 0.5px;
    white-space: nowrap;
  }
  .front-email {
    position: absolute;
    right: 40px;
    top: 290px;
    margin: 0;
    font-size: 12px;
    letter-spacing: 2px;
    color: var(--muted);
    white-space: nowrap;
  }

  /* Back */
  .back-contact {
    position: absolute;
    right: 0;
    top: 0;
    width: 300px;
    height: 400px;
    background: var(--pink);
    display: flex;
    flex-direction: column;
    justify-content: center;
    gap: 34px;
    padding-left: 28px;
    box-sizing: border-box;
  }
  .contact-row {
    display: flex;
    align-items: center;
    gap: 16px;
    color: var(--white);
    font-size: 14px;
    white-space: nowrap;
  }
  .contact-row svg { width: 22px; height: 22px; flex: none; }
  .card--back .brand-mark { left: 40px; top: 45px; }
  .identity {
    position: absolute;
    left: 40px;
    bottom: 55px;
    width: 330px;
  }
  .identity__name {
    font-family: "Russo One", "Arial Black", sans-serif;
    font-weight: 400;
    font-size: 42px;
    line-height: 1;
    color: var(--ink);
    margin: 0;
    white-space: nowrap;
  }
  .identity__role {
    font-style: italic;
    font-size: 20px;
    color: var(--ink);
    margin: 6px 0 0;
    text-align: right;
    white-space: nowrap;
  }
</style>
</head>
<body>
<main class="sheet">

  <section class="card card--front" aria-label="Business card front">
    <svg class="front-split" viewBox="0 0 700 400" aria-hidden="true">
      <polygon points="0,0 390,0 240,400 0,400" fill="var(--cream)"/>
    </svg>
    <div class="brand-mark">
      <span class="brand-mark__square"></span>
      <span class="brand-mark__name">Mira Bloom</span>
    </div>
    <p class="front-email">tessa.brogan@quellmail.com</p>
  </section>

  <section class="card card--back" aria-label="Business card back">
    <div class="brand-mark">
      <span class="brand-mark__square"></span>
      <span class="brand-mark__name">Mira Bloom</span>
    </div>
    <div class="identity">
      <h1 class="identity__name">Tessa Brogan</h1>
      <p class="identity__role">Personal Trainer</p>
    </div>
    <div class="back-contact">
      <div class="contact-row">
        <svg viewBox="0 0 24 24" aria-hidden="true"><path fill="var(--white)" d="M6.6 10.8c1.4 2.8 3.8 5.1 6.6 6.6l2.2-2.2c.3-.3.7-.4 1-.2 1.1.4 2.3.6 3.6.6.6 0 1 .4 1 1V20c0 .6-.4 1-1 1C10.6 21 3 13.4 3 4c0-.6.4-1 1-1h3.5c.6 0 1 .4 1 1 0 1.3.2 2.5.6 3.6.1.3 0 .7-.2 1z"/></svg>
        <span>07700218493</span>
      </div>
      <div class="contact-row">
        <svg viewBox="0 0 24 24" aria-hidden="true"><circle cx="12" cy="12" r="10" fill="var(--white)"/></svg>
        <span>www.Snapgram/ Mira Bloom</span>
      </div>
      <div class="contact-row">
        <svg viewBox="0 0 24 24" aria-hidden="true"><rect x="2" y="5" width="20" height="14" fill="none" stroke="var(--white)" stroke-width="2"/><path d="M2 5l10 8 10-8M2 19l7-7M22 19l-7-7" fill="none" stroke="var(--white)" stroke-width="1.6"/></svg>
        <span>tessa.brogan@quellmail.com</span>
      </div>
    </div>
  </section>

</main>
</body>
</html>
```